In need of a Wordpress website for a Water Sports Rental Company!

We are starting a new venture that provides a variety of rental equipment in the Cayman Islands. We are in need of a website where guests are able to book their rental gear during their stay in Cayman. We will also have an interactive map where guests can learn about off the beaten path activities to explore in here Cayman.

Our target market is middle/upper class, so we need a website that appeals to this group. We need our website to be clean, simple and easy to navigate. We need it to be highly visual and modern. We like the idea of the website having a tropical feel to it, we are very open to creative ideas that reflects this!

Must be designed in WordPress using the Velmora template I’ve provided.

You will find all instructions & the photos I want to use for this website on the following stashvo account:
- www.stashvo.com
- Username: hello@lumentrips.com
- Password: pelican7

All of the photos will need to be resized accordingly to be as small as possible without loosing resolution.

These are the tabs that will be used:
- Home Page
- Adventure Map
- Rental Gear
- Tours
- Photo Gallery
- Contact Us

Home Page
- You will find all the text and instructions for the home page in the word document named ‘Home Page’.

Adventure Map
- You will find all the text and instructions for the home page in the word document named ‘Adventure Map Content’
- There will also be a few 'guide' pages under this tab, which we will go in to detail with the winner.

Rentals
- You will find all the text and instructions for the Rentals page in the word document named ‘Rentals Content’

Tours
- This will just be a page saying ‘kayaking, snorkeling & Bioluminescence tours coming soon’.

Photo Gallery
- You will find the photos for this in our Stashvo.com Account

Contact Us
- Send us a Message – page will be similar to our other site http://lumentrips.com/contact/
- Phone: +1 (345) 555 0192
- Email: hello@tidalotterco.com

The big factors on who will have the winning design are:
- The background used
- The layout of the Home Page
- The animations at the top of the Rental Landing Page
- The overall clean, professional look to the website

If you have any questions, don't hesitate to ask.

We look forward to working with you all!!

Good luck!!

Target Market(s)

Middle/Upper Class on vacation with their family

Industry/Entity Type

It Company

Coding

Coded - Design and coding required

Number of Pages Required

5+ page

Colors
fffbf0
cadf82
fbf289
f6faec
fdf9cf
eaf2ce
fff3d1
fee18a
abd037

Requirements
Must have
• - Must be designed in Wordpress using the Velmora template I have provided or another suitable web template.
• - Must be Responsive Web Design so that the website adjusts to various screen sizes.

```html
<!DOCTYPE html>
<html lang="en">
<head>
<meta charset="utf-8">
<title>Tidal Otter Cayman — Adventure and Rental Company</title>
<link rel="stylesheet" href="https://fonts.googleapis.com/css2?family=Open+Sans:wght@400;600;700&family=Lora:ital,wght@1,600&display=swap">
<style>
:root{
  --green:#9cc43a;
  --green-dark:#7fa82a;
  --ink:#333333;
  --text:#777777;
  --muted:#9a9a9a;
  --line:#e6e6e6;
  --page:#ffffff;
  --soft:#f6faec;
  --footer:#2a2a2a;
  --footer-deep:#1e1e1e;
  --footer-text:#a8a8a8;
  --tweet:#29a9e1;
  --sea:#2aa6c9;
  --sand:#efe4c8;
}
*{box-sizing:border-box;margin:0;padding:0}
html,body{width:1200px;height:4476px;overflow:hidden}
body{position:relative;background:var(--page);font-family:"Open Sans",Arial,sans-serif;color:var(--text);font-size:13px;line-height:1.6}
a{color:inherit;text-decoration:none}

/* header */
.site-header{position:absolute;top:0;left:0;width:1200px;height:260px;text-align:center}
.brand{position:absolute;top:22px;left:0;width:1200px;display:flex;justify-content:center;align-items:center;gap:14px}
.brand-mark{width:64px;height:64px;border-radius:50%;background:var(--green)}
.brand-name{font-family:"Open Sans",Arial,sans-serif;font-weight:700;font-size:30px;color:var(--ink);letter-spacing:1px}
.tagline{position:absolute;top:118px;left:0;width:1200px;font-family:"Lora",Georgia,serif;font-style:italic;font-weight:600;font-size:28px;color:var(--green-dark)}
.main-nav{position:absolute;top:208px;left:0;width:1200px;display:flex;justify-content:center;gap:46px;font-size:14px;color:var(--text)}
.main-nav a.current{color:var(--green);font-weight:600}
.header-rule{position:absolute;top:250px;left:0;width:1200px;height:1px;background:var(--line)}

/* hero */
.hero{position:absolute;top:260px;left:0;width:1200px;height:420px;background:linear-gradient(180deg,#bfe3f2 0%,#7cc7e0 30%,#2aa6c9 48%,#6fd0d6 60%,#efe4c8 72%,#f5ecd6 100%)}
.hero-arrow{position:absolute;top:190px;width:40px;height:40px}
.hero-arrow.prev{left:20px}.hero-arrow.next{right:20px}
.hero-play{position:absolute;top:180px;left:580px;width:40px;height:40px}

/* intro cards */
.intro-cards{position:absolute;top:690px;left:130px;width:940px;display:flex;gap:20px}
.intro-card{width:300px}
.intro-card .photo{height:180px}
.intro-card h3{margin-top:16px;font-weight:400;font-size:20px;color:var(--green)}
.intro-card p{margin-top:6px;font-size:11px;line-height:1.55;color:var(--muted)}

/* welcome */
.welcome{position:absolute;top:1050px;left:130px;width:940px;text-align:center}
.welcome h2{font-weight:400;font-size:21px;color:var(--green)}
.welcome p{margin-top:12px;font-size:12px;line-height:1.65;color:var(--text)}

/* feature rows */
.feature{position:absolute;left:150px;width:900px;height:230px;background:#fff;display:flex;align-items:center;gap:36px;padding:0 24px;box-shadow:0 14px 16px -12px rgba(0,0,0,.28)}
.feature.reverse{flex-direction:row-reverse}
.feature .photo{flex:0 0 240px;height:170px}
.feature .copy{flex:1}
.feature h3{font-weight:400;font-size:22px;line-height:1.3;color:var(--ink)}
.feature p{margin-top:12px;font-size:12px;line-height:1.7;color:var(--text)}
.feature p .more{color:var(--green);font-weight:600}

/* top picks */
.picks-title{position:absolute;top:3320px;left:0;width:1200px;text-align:center;font-weight:400;font-size:21px;color:var(--green)}
.picks{position:absolute;top:3370px;left:130px;width:940px;display:flex;gap:20px}
.pick{width:220px}
.pick .photo{height:140px}
.pick h4{margin-top:12px;font-weight:400;font-size:18px;color:var(--green)}
.pick p{margin-top:4px;font-size:10.5px;line-height:1.55;color:var(--muted)}
.pick .read{display:block;margin-top:8px;font-size:11px;font-weight:700;color:var(--ink)}

/* partners */
.partners{position:absolute;top:3740px;left:130px;width:940px;display:flex;justify-content:space-between;align-items:center;height:80px}
.partner{font-size:24px;font-weight:600;color:#7d7d7d;letter-spacing:1px}

/* tweet band */
.tweet-band{position:absolute;top:3860px;left:0;width:1200px;height:64px;background:var(--tweet);color:#fff;display:flex;justify-content:center;align-items:center;gap:14px;font-size:14px}
.tweet-band .dot{width:18px;height:18px;border-radius:50%;background:#fff;opacity:.9}

/* footer */
.site-footer{position:absolute;top:3924px;left:0;width:1200px;height:512px;background:var(--footer);color:var(--footer-text)}
.footer-cols{position:absolute;top:56px;left:130px;width:940px;display:flex;gap:40px}
.footer-col{width:205px;font-size:11px;line-height:1.7}
.footer-col h5{font-size:15px;font-weight:600;color:#ffffff;margin-bottom:16px}
.footer-brand{display:flex;align-items:center;gap:10px;margin-bottom:16px}
.footer-brand .brand-mark{width:44px;height:44px}
.footer-brand span{font-weight:700;font-size:16px;color:#fff}
.gallery-grid{display:grid;grid-template-columns:repeat(3,62px);gap:6px}
.gallery-grid .photo{height:62px}
.post-list li{list-style:none;padding:5px 0;border-bottom:1px solid #3a3a3a}
.contact-list li{list-style:none;display:flex;gap:10px;align-items:flex-start;padding:6px 0}
.contact-list svg{flex:0 0 14px;margin-top:3px}
.social{position:absolute;top:432px;right:130px;display:flex;gap:14px}
.social span{width:22px;height:22px;border-radius:50%;background:#555}
.bottom-bar{position:absolute;top:4436px;left:0;width:1200px;height:40px;background:var(--footer-deep);color:#888;font-size:11px;line-height:40px;padding-left:130px}
</style>
</head>
<body>

<header class="site-header">
  <div class="brand"><span class="brand-mark"></span><span class="brand-name">Tidal Otter Cayman</span></div>
  <div class="tagline">Cayman's Premier Adventure and Rental Company</div>
  <nav class="main-nav">
    <a class="current" href="#">Home</a>
    <a href="#">Rental Gear</a>
    <a href="#">Adventure Map</a>
    <a href="#">Tours</a>
    <a href="#">Photo Gallery</a>
    <a href="#">Contact Us</a>
  </nav>
  <div class="header-rule"></div>
</header>

<section class="hero" role="img" aria-label="Blue kayaks arranged in a circle on a white sand beach by turquoise water">
  <svg class="hero-arrow prev" viewBox="0 0 40 40"><rect width="40" height="40" fill="rgba(0,0,0,.35)"/><path d="M24 12l-8 8 8 8" stroke="#fff" stroke-width="3" fill="none"/></svg>
  <svg class="hero-play" viewBox="0 0 40 40"><circle cx="20" cy="20" r="19" fill="rgba(255,255,255,.85)"/><path d="M16 12l12 8-12 8z" fill="#2aa6c9"/></svg>
  <svg class="hero-arrow next" viewBox="0 0 40 40"><rect width="40" height="40" fill="rgba(0,0,0,.35)"/><path d="M16 12l8 8-8 8" stroke="#fff" stroke-width="3" fill="none"/></svg>
</section>

<section class="intro-cards">
  <article class="intro-card">
    <div class="photo" role="img" aria-label="Kayakers paddling across clear shallow water" style="background:linear-gradient(180deg,#9fd6ea,#3fb4c9 55%,#cde9d8)"></div>
    <h3>Exploration</h3>
    <p>Discover quiet coves, hidden reefs and mangrove trails at your own pace. Our gear and maps help you find the island's best kept secrets with ease.</p>
  </article>
  <article class="intro-card">
    <div class="photo" role="img" aria-label="Paddle boards resting on calm sea near the shore" style="background:linear-gradient(180deg,#bfe5f3,#4ec0d6 50%,#e9dfc1)"></div>
    <h3>Relaxation</h3>
    <p>Slow down and soak up the sun on warm water. Float, paddle or simply rest on the sand while we take care of every detail of your rental day.</p>
  </article>
  <article class="intro-card">
    <div class="photo" role="img" aria-label="Snorkellers over a coral reef" style="background:linear-gradient(180deg,#5bc3d8,#1f8fb2 60%,#2d7c8e)"></div>
    <h3>Education</h3>
    <p>Learn about local marine life, reef care and island history. Our guides share stories and tips so every outing leaves you knowing a little more.</p>
  </article>
</section>

<section class="welcome">
  <h2>Welcome to Tidal Otter Cayman!</h2>
  <p>We love sharing the freedom to explore what is waiting out there on Grand Cayman's shores and waters. We are a rental company offering everything you need to make the most of your vacation. Our website serves as a great starting point to help you prepare for your island adventure, with rental booking, guides and tips. We feature a large selection of adventures on our interactive map with tons of useful information, pictures and directions, so you can plan each day with confidence.</p>
</section>

<article class="feature" style="top:1300px">
  <div class="photo" role="img" aria-label="Rental kayaks lined up on a beach" style="background:linear-gradient(180deg,#a9dcef,#35aac6 55%,#e8dcbc)"></div>
  <div class="copy">
    <h3>Your one stop shop for all the rentals you need here in Cayman!</h3>
    <p>We have a huge range of fun toys and equipment for you to enjoy. Whether it's for exploring or relaxing, we have all the equipment you need to make the most of your stay here in Cayman. Reserve what you like, pick it up and go enjoy the island at your own pace. <span class="more">Check Out Our Rentals</span></p>
  </div>
</article>

<article class="feature reverse" style="top:1590px">
  <div class="photo" role="img" aria-label="Illustrated adventure map of Grand Cayman" style="background:linear-gradient(135deg,#bfe6f0,#8fd0e0 50%,#d9ecc0)"></div>
  <div class="copy">
    <h3>Check out our interactive map of Cayman!</h3>
    <p>You won't find any tourist traps on our map! We're all about getting off the beaten path and finding those unique spots and unusual activities to explore. Use our expert advice on which adventures are best for you and how to tackle them! <span class="more">View Our Adventures</span></p>
  </div>
</article>

<article class="feature" style="top:1880px">
  <div class="photo" role="img" aria-label="Clear bottom kayak floating over turquoise water" style="background:linear-gradient(180deg,#7fd0e2,#2d9fc0 60%,#1f7e9c)"></div>
  <div class="copy">
    <h3>Enjoy Complete freedom to explore.</h3>
    <p>Inflatable kayaks have revolutionised the way kayak exploration is done in a way never before. Our kayaks give you the freedom to explore Cayman's most secluded locations and snorkel spots, all while being light, comfortable and easy to use. <span class="more">View Our Kayaks</span></p>
  </div>
</article>

<article class="feature reverse" style="top:2170px">
  <div class="photo" role="img" aria-label="Beach cruiser bicycles parked by the sea" style="background:linear-gradient(180deg,#cdebf5,#8fd3e4 55%,#efe6cf)"></div>
  <div class="copy">
    <h3>There's no easier way to get around the island.</h3>
    <p>What better way is there to explore the island other than to rent a bike and go? Our mountain bikes are perfect for those interested in heading out on a full day adventure. If you're looking for something more casual, renting a cruiser is perfect to get around the Seven Mile Beach area. Use our map to help guide you to our suggested locations. <span class="more">Take A Look At Bikes</span></p>
  </div>
</article>

<article class="feature" style="top:2470px">
  <div class="photo" role="img" aria-label="Paddle boarder gliding over a calm lagoon" style="background:linear-gradient(180deg,#b6e2f2,#4bb6d1 55%,#2f95b0)"></div>
  <div class="copy">
    <h3>We want to be your personal concierge and help you to plan out your trip!</h3>
    <p>When we come to deliver your equipment, we teach you everything you need to know about the island including the best hidden spots, best restaurants and bars to eat and drink, anything else you might be curious about. Please don't hesitate to contact us for any and all of your vacation questions. We are happy to help! <span class="more">Get Into Our Contact Us</span></p>
  </div>
</article>

<article class="feature reverse" style="top:2760px">
  <div class="photo" role="img" aria-label="Floating hammock boat on blue water" style="background:linear-gradient(180deg,#aee0ef,#3fb0cb 55%,#2a8fae)"></div>
  <div class="copy">
    <h3>Is it a boat? Is it a whale?.... It's a Driftnest!</h3>
    <p>Easily one of the coolest inventions we've come across, the Driftnest is a versatile toy the whole family can enjoy together. Spend the day cruising along Seven Mile Beach or take us on our map with your crew. Better still, bring a cooler on board and put the kids to work paddling as you relax in your hammock on the crystal clear waters! <span class="more">Rent A Driftnest</span></p>
  </div>
</article>

<article class="feature" style="top:3050px">
  <div class="photo" role="img" aria-label="Snorkel mask and underwater reef view" style="background:linear-gradient(180deg,#e58fc4,#a67fd6 45%,#3fa6cc)"></div>
  <div class="copy">
    <h3>A new way to Snorkel!</h3>
    <p>Our full face snorkel masks are easy to use, making them perfect for kids and beginners. You simply put the mask on and breathe as you usually would. There's no need to get used to breathing from your mouth and you don't experience a sore jaw from having to hold the mouth piece in place. Just ask and we'll bring one along for you to try! <span class="more">Get Yours Here</span></p>
  </div>
</article>

<h2 class="picks-title">Our Adventure Top Picks</h2>
<section class="picks">
  <article class="pick">
    <div class="photo" role="img" aria-label="Glowing blue bioluminescent bay at night" style="background:linear-gradient(180deg,#0d1b3a,#15407a 60%,#2a8ad0)"></div>
    <h4>Bio Bay</h4>
    <p>Paddle into the night and watch the water glow around you. One of the island's most magical sights, best seen on a dark evening.</p>
    <a class="read" href="#">Read More</a>
  </article>
  <article class="pick">
    <div class="photo" role="img" aria-label="Sunken ship wreck seen underwater" style="background:linear-gradient(180deg,#3aa9c4,#1f7b98 60%,#165e78)"></div>
    <h4>Kittiwake</h4>
    <p>Snorkel above a historic wreck resting in shallow water. Its decks are home to colourful fish and make for a stunning swim.</p>
    <a class="read" href="#">Read More</a>
  </article>
  <article class="pick">
    <div class="photo" role="img" aria-label="Small sandy islet surrounded by turquoise water" style="background:linear-gradient(180deg,#bfe6f3,#55c3d6 50%,#efe3c3)"></div>
    <h4>Sand Cay Island</h4>
    <p>A tiny island of white sand and palms just offshore. Kayak over for a picnic and a swim along its calm, protected reef edge.</p>
    <a class="read" href="#">Read More</a>
  </article>
  <article class="pick">
    <div class="photo" role="img" aria-label="Shallow sandbar with clear water" style="background:linear-gradient(180deg,#8fd7e6,#3ab2cc 55%,#d7e8d0)"></div>
    <h4>Stingray City</h4>
    <p>Stand in waist deep water on the sandbar and meet the gentle locals. A classic Cayman outing that the whole family will love.</p>
    <a class="read" href="#">Read More</a>
  </article>
</section>

<section class="partners" aria-label="Partners">
  <span class="partner">HALVERN</span>
  <span class="partner">Quorra</span>
  <span class="partner">NEXTA</span>
  <span class="partner">Marlowe</span>
  <span class="partner">Orbline</span>
</section>

<section class="tweet-band">
  <span class="dot"></span>
  <span>Proin ipsum dapibus gravida, et tristique tristique nulla eget hendrerit vestibulum pulvinar</span>
</section>

<footer class="site-footer">
  <div class="footer-cols">
    <div class="footer-col">
      <div class="footer-brand"><span class="brand-mark"></span><span>Tidal Otter Cayman</span></div>
      <p>Tidal Otter Cayman is your one stop shop for water sports rentals, island adventures and local tips. We help families explore Grand Cayman beyond the usual tourist routes.</p>
    </div>
    <div class="footer-col">
      <h5>Gallery</h5>
      <div class="gallery-grid">
        <div class="photo" role="img" aria-label="Gallery photo of the sea" style="background:#3aa9c4"></div>
        <div class="photo" role="img" aria-label="Gallery photo of a beach" style="background:#d9cfae"></div>
        <div class="photo" role="img" aria-label="Gallery photo of kayaks" style="background:#2f7fb8"></div>
        <div class="photo" role="img" aria-label="Gallery photo of a reef" style="background:#2a8fa6"></div>
        <div class="photo" role="img" aria-label="Gallery photo of palms" style="background:#6f9a58"></div>
        <div class="photo" role="img" aria-label="Gallery photo of a sunset" style="background:#c98a5a"></div>
      </div>
    </div>
    <div class="footer-col">
      <h5>Recent Posts</h5>
      <ul class="post-list">
        <li>» Hidden lagoons of the east end</li>
        <li>» A guide to island cycling</li>
        <li>» Best sunset paddles</li>
        <li>» Family snorkel spots</li>
        <li>» What to pack for the reef</li>
        <li>» Night tours at the bay</li>
        <li>» Meet our rental team</li>
        <li>» Tips for new paddlers</li>
      </ul>
    </div>
    <div class="footer-col">
      <h5>Contact Us</h5>
      <ul class="contact-list">
        <li><svg width="14" height="14" viewBox="0 0 14 14"><path d="M7 1a4 4 0 0 0-4 4c0 3 4 8 4 8s4-5 4-8a4 4 0 0 0-4-4zm0 5.5A1.5 1.5 0 1 1 7 3.5a1.5 1.5 0 0 1 0 3z" fill="#9cc43a"/></svg><span>18 Coral Bay Road, West End<br>Grand Cayman</span></li>
        <li><svg width="14" height="14" viewBox="0 0 14 14"><path d="M3 1l2.5 3-1.5 1.5a8 8 0 0 0 4.5 4.5L10 8.5l3 2.5-1.5 2C6 13 1 8 1 2.5z" fill="#9cc43a"/></svg><span>+1 (345) 555 0192</span></li>
        <li><svg width="14" height="14" viewBox="0 0 14 14"><rect x="1" y="3" width="12" height="8" fill="none" stroke="#9cc43a" stroke-width="1.4"/><path d="M1 3l6 5 6-5" fill="none" stroke="#9cc43a" stroke-width="1.4"/></svg><span>hello@tidalotterco.com</span></li>
      </ul>
    </div>
  </div>
  <div class="social" aria-label="Social links"><span></span><span></span><span></span><span></span><span></span><span></span></div>
</footer>
<div class="bottom-bar">Copyright © 2017 Tidal Otter Cayman · All rights reserved</div>

</body>
</html>
```